Business Card

Just need business logo with phone number on it. 0487 312 654
And the following on the bottom of the card.

"Your local plumbing experts".
and emblems for zelpa card, cheque and cash

```html
<!DOCTYPE html>
<html lang="en">
<head>
<meta charset="utf-8">
<title>Harbourline Plumbing – Business Card</title>
<link href="https://fonts.googleapis.com/css2?family=Roboto:ital,wght@0,400;0,700;1,400&display=swap" rel="stylesheet">
<style>
  :root {
    --stage: #e5e5e5;
    --card-white: #f9f9f9;
    --brand-red: #da251d;
    --brand-blue: #0079c1;
    --tag-dark: #323538;
    --ink-white: #ffffff;
  }
  * { margin: 0; padding: 0; box-sizing: border-box; }
  html, body {
    width: 1200px; height: 608px; overflow: hidden;
    background: var(--stage);
    font-family: "Roboto", Arial, sans-serif;
  }
  .stage { position: relative; width: 1200px; height: 608px; }

  .card { position: absolute; top: 206px; width: 327px; height: 197px; overflow: hidden; }

  /* Front */
  .card-front { left: 237px; background: var(--card-white); }
  .card-front .brand-name {
    position: absolute; left: 0; right: 0; top: 86px;
    text-align: center; color: var(--brand-red);
    font-weight: 700; font-size: 20px; letter-spacing: 0.5px;
  }

  /* Back */
  .card-back { left: 635px; background: var(--brand-blue); }
  .card-back .panels { position: absolute; inset: 0; }
  .card-back .brand-name {
    position: absolute; left: 18px; width: 162px; top: 38px;
    text-align: center; color: var(--ink-white);
    font-weight: 700; font-size: 17px; line-height: 1.15;
  }
  .person { position: absolute; left: 18px; top: 96px; color: var(--ink-white); }
  .person-name { font-weight: 700; font-size: 14px; }
  .person-role { font-style: italic; font-size: 9px; margin-top: 3px; }

  .contacts { position: absolute; left: 18px; top: 141px; color: var(--ink-white); list-style: none; }
  .contacts li { display: flex; align-items: center; gap: 4px; font-size: 8.8px; line-height: 11px; }
  .contacts li.phone { font-size: 10.5px; font-weight: 700; margin-bottom: 2px; }
  .contacts svg { width: 8px; height: 8px; fill: var(--ink-white); flex: none; }

  .tagline {
    position: absolute; left: 193px; top: 178px;
    color: var(--ink-white); font-size: 9.6px; line-height: 14px;
  }
</style>
</head>
<body>
<main class="stage">
  <section class="card card-front" aria-label="Card front">
    <div class="brand-name">Harbourline Plumbing</div>
  </section>

  <section class="card card-back" aria-label="Card back">
    <svg class="panels" viewBox="0 0 327 197" width="327" height="197" aria-hidden="true">
      <polygon points="0,0 250,0 190,104 190,189 0,189" fill="var(--brand-red)"/>
      <polygon points="176,176 327,176 327,197 158,197" fill="var(--tag-dark)"/>
    </svg>

    <div class="brand-name">Harbourline<br>Plumbing</div>

    <div class="person">
      <div class="person-name">Liam Carter</div>
      <div class="person-role">Plumber</div>
    </div>

    <ul class="contacts">
      <li class="phone">
        <svg viewBox="0 0 10 10"><path d="M1 3c0-1 1-2 4-2s4 1 4 2v1H7V3H3v1H1zM2 5h6l1 4H1z"/></svg>
        0487 312 654
      </li>
      <li>
        <svg viewBox="0 0 10 10"><path d="M0 2h10v6H0zM1 3v.4l4 2.6 4-2.6V3L5 5.4z" fill-rule="evenodd"/></svg>
        liam@harbourline.com
      </li>
      <li>
        <svg viewBox="0 0 10 10"><path d="M5 0a5 5 0 1 0 0 10A5 5 0 0 0 5 0zm0 1c.8 0 1.5 1.5 1.6 3.5H3.4C3.5 2.5 4.2 1 5 1zM1 5.5h1.6c.1 1.4.4 2.4.9 3.1A4 4 0 0 1 1 5.5zm2.4 0h3.2C6.5 7.5 5.8 9 5 9s-1.5-1.5-1.6-3.5zm4 0H9a4 4 0 0 1-2.5 3.1c.5-.7.8-1.7.9-3.1zM1 4.5a4 4 0 0 1 2.5-3.1c-.5.7-.8 1.7-.9 3.1zm6.4 0c-.1-1.4-.4-2.4-.9-3.1A4 4 0 0 1 9 4.5z"/></svg>
        www.harbourline.com
      </li>
    </ul>

    <div class="tagline">Your Local Plumbing Experts</div>
  </section>
</main>
</body>
</html>
```